Professional and creative business card design for recruiting service providers

Our company supports German medium-sized companies in filling vacancies promptly. For this we use social media marketing and bring our customers into the visibility.

We want a professional but also creative design for our business cards.

Please look at lindqvar-staff.de to get an impression of our CI.

Target Market(s)

Small and medium-sized companies in Germany from the industry

Industry/Entity Type

Industrie, Handwerk

Contact Information for Business Card

Name, Position, Telefonnummer, Email, Website

Colors
EE7325
F08F49
F5BC92
FAE3D3
FDF4ED

Requirements
Must have
• A picture of the employee and in the style of www.lindqvar-staff.de

```html
<!DOCTYPE html>
<html lang="de">
<head>
<meta charset="utf-8">
<title>Lindqvar Staff – Visitenkarten</title>
<link rel="stylesheet" href="https://fonts.googleapis.com/css2?family=Montserrat:wght@700;800&family=Arimo:wght@400;700&display=swap">
<style>
  :root {
    --orange: #ee7325;
    --orange-soft: #f08f49;
    --peach: #f5bc92;
    --ink: #222222;
    --text: #333333;
    --card-light: #f6f6f6;
    --card-dark: #2a2a2a;
    --stage: #e4e4e4;
  }
  * { box-sizing: border-box; margin: 0; padding: 0; }
  html, body { width: 1200px; height: 856px; overflow: hidden; }
  body {
    background: var(--stage);
    display: flex;
    align-items: center;
    justify-content: center;
    gap: 44px;
    font-family: "Arimo", Arial, sans-serif;
  }
  .card {
    width: 540px;
    height: 350px;
    position: relative;
    overflow: hidden;
    box-shadow: 0 10px 28px rgba(0,0,0,.18);
  }
  .card--front { background: var(--card-light); }
  .card--back {
    background: var(--card-dark);
    display: flex;
    align-items: center;
    justify-content: center;
  }
  .brand {
    display: flex;
    align-items: center;
    gap: 12px;
    font-family: "Montserrat", sans-serif;
    font-weight: 800;
    letter-spacing: .04em;
    text-transform: uppercase;
    line-height: 1;
  }
  .brand__mark { width: 22px; height: 22px; background: var(--orange); flex: none; }
  .card--front .brand { position: absolute; left: 34px; top: 34px; font-size: 24px; color: var(--ink); }
  .card--back .brand { font-size: 36px; color: #ffffff; gap: 18px; }
  .card--back .brand__mark { width: 32px; height: 32px; }
  .details { position: absolute; left: 34px; top: 96px; color: var(--text); }
  .details__name {
    font-family: "Arimo", sans-serif;
    font-weight: 700;
    font-size: 19px;
    letter-spacing: .03em;
    color: var(--orange);
    text-transform: uppercase;
  }
  .details__role { font-size: 15px; margin-top: 3px; }
  .details__address { font-size: 15px; line-height: 1.3; margin-top: 16px; }
  .contact { list-style: none; margin-top: 14px; font-size: 15px; line-height: 1.4; }
  .contact li { display: flex; align-items: center; gap: 8px; }
  .contact svg { width: 13px; height: 13px; flex: none; }
  .portrait {
    position: absolute;
    right: 0;
    bottom: 0;
    width: 260px;
    height: 250px;
    background: linear-gradient(160deg, #c79a7e 0%, #8a6a58 28%, #1d1d1d 48%, #111111 100%);
  }
</style>
</head>
<body>
  <section class="card card--front" aria-label="Visitenkarte Vorderseite">
    <div class="brand"><span class="brand__mark"></span><span>Lindqvar Staff</span></div>
    <div class="details">
      <p class="details__name">Tobias Renner</p>
      <p class="details__role">Manager</p>
      <p class="details__address">Lindenauer Straße 42<br>70176 Stuttgart</p>
      <ul class="contact">
        <li>
          <svg viewBox="0 0 16 16"><path fill="var(--orange)" d="M3.6 1.2l2.3 2.6-1.2 1.9c.9 2 2.4 3.5 4.4 4.5l1.9-1.2 2.6 2.3-1.4 2.6C7.3 13.5 2.4 8.6 1.2 3z"/></svg>
          <span>0151 204 7739</span>
        </li>
        <li>
          <svg viewBox="0 0 16 16"><rect x="1.5" y="3.5" width="13" height="9" fill="none" stroke="var(--orange)" stroke-width="1.6"/><path d="M1.5 3.5L8 9l6.5-5.5" fill="none" stroke="var(--orange)" stroke-width="1.6"/></svg>
          <span>info@lindqvar-staff.de</span>
        </li>
        <li>
          <svg viewBox="0 0 16 16"><circle cx="8" cy="8" r="6.5" fill="none" stroke="var(--orange)" stroke-width="1.5"/><ellipse cx="8" cy="8" rx="2.8" ry="6.5" fill="none" stroke="var(--orange)" stroke-width="1.3"/><path d="M1.5 8h13M2.5 5h11M2.5 11h11" stroke="var(--orange)" stroke-width="1.2"/></svg>
          <span>www.lindqvar-staff.de</span>
        </li>
      </ul>
    </div>
    <div class="portrait" role="img" aria-label="Porträtfoto des Mitarbeiters im dunklen Rollkragenpullover"></div>
  </section>

  <section class="card card--back" aria-label="Visitenkarte Rückseite">
    <div class="brand"><span class="brand__mark"></span><span>Lindqvar Staff</span></div>
  </section>
</body>
</html>
```